Yacht, Boats, Watersports company needs a redesign of business card

Hello Designers!
We are a Boat dealership company that sells fun in the water, we sell boats, Yachts, Kayaks and also yacht WaterSport toys. We are looking to redesign our business cards in to something a little bit more sophisticated. in a way that we can make better use of our company colors. I'm attaching a zipped file containing the company 3 sets of company logo which one is an horizontal another one is a vertical and also a chromed 3d logo. Also is included two set of business cards that we use and also some designs that i think it's interesting. We use PMS 2026c Orange and PMS 7687C Blue. I would like to see at least two different options with the orange as accent and also using blue as an accent color. It's really important for the business cards to have a font option and size that is legible to most people. Our current website is wwww.coralpennant.com. Please visit if you want to have a better feeling of the Boat dealership
You can send Single sided or double side options. We are now using single sided but we may be open for a double side option if we really like the design.
Target Market(s)
Marine, boat sales, yacht sales, water toys sales/
Contact Information for Business Card
Name: Dale Whitcombe
Address: 212 North Fenwick Lane,
Palm Cove, GA 31520
Phone: 555-731-8842
Fax: 555:731-8843
Cell: 555-382-1490
Email: dw@coralpennant.com
Website: coralpennant.com
Requirements
Must have
- the current information of the business card provided.
logo
use the PMS Colors
Nice to have
- a touch of elegance and sophistication but simple
Should not have
- should not have any typography that is hard to read, the card should be simple but yet sophisticated.

```html
<!DOCTYPE html>
<html lang="en">
<head>
<meta charset="utf-8">
<title>Coral Pennant — Business Card</title>
<link rel="stylesheet" href="https://fonts.googleapis.com/css2?family=Michroma&family=Arimo:wght@400&display=swap">
<style>
  :root {
    --backdrop: #2a2a2a;
    --card: #0d0d0d;
    --orange: #e8632b;
    --blue: #1f5ca6;
    --ink: #cfcfcf;
    --silver: #d9d9d9;
    --rule: #4a4a4a;
  }
  * { box-sizing: border-box; margin: 0; padding: 0; }
  html, body { width: 1200px; height: 900px; overflow: hidden; }
  body {
    background: radial-gradient(ellipse at 50% 40%, #3a3a3a 0%, var(--backdrop) 60%, #161616 100%);
    display: flex; align-items: center; justify-content: center; gap: 60px;
    font-family: "Arimo", Arial, sans-serif;
  }
  .card {
    width: 525px; height: 300px; background: var(--card);
    border-radius: 22px; box-shadow: 0 18px 40px rgba(0,0,0,.6);
    position: relative; overflow: hidden;
  }
  /* front */
  .card-front { display: flex; align-items: center; }
  .brand-block {
    width: 235px; height: 100%;
    display: flex; flex-direction: column; align-items: center; justify-content: center; gap: 14px;
  }
  .brand-mark { width: 60px; height: 60px; }
  .brand-name {
    font-family: "Michroma", sans-serif; font-size: 14px; letter-spacing: 1px;
    color: var(--blue); text-transform: uppercase; white-space: nowrap;
  }
  .divider { width: 1px; height: 150px; background: var(--rule); }
  .contact-block { padding-left: 24px; padding-right: 20px; }
  .person-name {
    font-family: "Michroma", sans-serif; font-size: 15px; font-weight: 400; letter-spacing: 1px;
    text-transform: uppercase; margin-bottom: 12px; white-space: nowrap;
  }
  .person-name .first { color: var(--blue); }
  .person-name .last { color: var(--orange); }
  .contact-list { list-style: none; }
  .contact-list li {
    display: flex; align-items: center; gap: 9px;
    font-size: 13px; line-height: 19px; color: var(--ink); white-space: nowrap;
  }
  .contact-list svg { width: 12px; height: 12px; fill: var(--blue); flex: none; }
  .address { margin-top: 14px; font-size: 13px; line-height: 18px; color: var(--ink); }
  /* back */
  .card-back { display: flex; align-items: center; justify-content: center; gap: 18px; }
  .card-back .brand-mark { width: 72px; height: 72px; }
  .card-back .brand-name { color: var(--silver); font-size: 17px; }
</style>
</head>
<body>
  <section class="card card-front">
    <div class="brand-block">
      <svg class="brand-mark" viewBox="0 0 60 60" aria-hidden="true">
        <circle cx="30" cy="30" r="26" fill="none" stroke="var(--orange)" stroke-width="5"/>
      </svg>
      <div class="brand-name">Coral Pennant</div>
    </div>
    <div class="divider"></div>
    <div class="contact-block">
      <h1 class="person-name"><span class="first">Dale</span> <span class="last">Whitcombe</span></h1>
      <ul class="contact-list">
        <li><svg viewBox="0 0 24 24"><path d="M6.6 10.8a15 15 0 0 0 6.6 6.6l2.2-2.2a1 1 0 0 1 1-.25 11.4 11.4 0 0 0 3.6.57 1 1 0 0 1 1 1V20a1 1 0 0 1-1 1A17 17 0 0 1 3 4a1 1 0 0 1 1-1h3.5a1 1 0 0 1 1 1c0 1.25.2 2.45.57 3.6a1 1 0 0 1-.25 1z"/></svg>555-731-8842</li>
        <li><svg viewBox="0 0 24 24"><path d="M6 2h12v6H6zM3 9h18a1 1 0 0 1 1 1v8h-4v4H6v-4H2v-8a1 1 0 0 1 1-1zm5 8v3h8v-3z"/></svg>555:731-8843</li>
        <li><svg viewBox="0 0 24 24"><path d="M7 1h10a2 2 0 0 1 2 2v18a2 2 0 0 1-2 2H7a2 2 0 0 1-2-2V3a2 2 0 0 1 2-2zm0 3v14h10V4z"/></svg>555-382-1490</li>
        <li><svg viewBox="0 0 24 24"><path d="M2 5h20v14H2zm2 2v.5l8 5 8-5V7z"/></svg>dw@coralpennant.com</li>
        <li><svg viewBox="0 0 24 24"><path d="M12 2a10 10 0 1 0 0 20 10 10 0 0 0 0-20zm-1 2.1V8H7.6A8 8 0 0 1 11 4.1zm2 0A8 8 0 0 1 16.4 8H13zM4.3 10h6.7v4H4.3a8 8 0 0 1 0-4zm8.7 0h6.7a8 8 0 0 1 0 4H13zm-5.4 6H11v3.9A8 8 0 0 1 7.6 16zM13 16h3.4a8 8 0 0 1-3.4 3.9z"/></svg>www.coralpennant.com</li>
      </ul>
      <p class="address">212 North Fenwick Lane,<br>Palm Cove, GA 31520</p>
    </div>
  </section>

  <section class="card card-back">
    <svg class="brand-mark" viewBox="0 0 60 60" aria-hidden="true">
      <circle cx="30" cy="30" r="26" fill="none" stroke="var(--silver)" stroke-width="4"/>
    </svg>
    <div class="brand-name">Coral Pennant</div>
  </section>
</body>
</html>
```